Home Remodeling company needs a business card design

we need a business card design for home remodeling company in hamilton county, indiana USA. we offers a wide range of construction services including whole house renovations, Design and Build Basements and Kitchen and Bathroom Remodeling . we would like to see designs for both site of business card that use the same color of the company logo and also including all information below :
1- Karim Feltous CEO / General Contractor
2- all company contacts Telephone numbers ( 1-888-DULOM-47 ) ( 317-555-0193) email address ( info@dulomhome.com) website ( www.dulomhome.com ) and social media logos (Facebook- twitter- google plus )
3- company logo
4- licensed . insured . bonded

```html
<!DOCTYPE html>
<html lang="en">
<head>
<meta charset="utf-8">
<title>Dulom Home Remodeling – Business Card</title>
<link href="https://fonts.googleapis.com/css2?family=Cabin:wght@400;500;600;700&display=swap" rel="stylesheet">
<style>
  :root {
    --backdrop: #9b9b9b;
    --card-light: #eeeef0;
    --card-dark: #353537;
    --ink: #333335;
    --accent: #c0222b;
    --paper-mark: #e4e4e6;
  }
  * { margin: 0; padding: 0; box-sizing: border-box; }
  html, body {
    width: 1105px; height: 1200px; overflow: hidden;
    background: var(--backdrop);
    font-family: "Cabin", "Gill Sans", sans-serif;
  }
  .card {
    position: absolute; left: 182px; width: 746px; height: 424px;
  }
  .card--front { top: 119px; background: var(--card-light); }
  .card--back { top: 637px; background: var(--card-dark); }

  .company-name {
    position: absolute; left: 46px; top: 52px;
    font-weight: 600; font-size: 40px; line-height: 1; color: var(--ink);
  }

  .contacts { position: absolute; left: 46px; top: 262px; list-style: none; }
  .contacts li {
    display: flex; align-items: center; gap: 10px;
    height: 29px; font-size: 19px; color: var(--ink);
  }
  .contacts svg { width: 18px; height: 18px; fill: var(--ink); flex: none; }

  .person { position: absolute; right: 48px; top: 276px; text-align: right; }
  .person__name { font-weight: 600; font-size: 25px; color: var(--ink); }
  .person__role { margin-top: 4px; font-size: 20px; color: var(--accent); }

  .edge { position: absolute; left: 0; right: 0; }
  .edge--red { top: 406px; height: 3px; background: var(--accent); }
  .edge--dark { top: 412px; height: 12px; background: var(--card-dark); }

  .back-mark {
    position: absolute; left: 0; right: 0; top: 118px;
    display: flex; flex-direction: column; align-items: center; gap: 14px;
  }
  .back-mark__square { width: 110px; height: 110px; background: var(--paper-mark); }
  .back-mark__name {
    font-weight: 600; font-size: 30px; line-height: 1; color: var(--paper-mark);
  }
  .credentials {
    position: absolute; left: 0; right: 0; top: 318px;
    text-align: center; font-size: 22px; color: #f2f2f2; letter-spacing: 0.5px;
  }
  .social {
    position: absolute; left: 0; right: 0; top: 362px;
    display: flex; justify-content: center; align-items: center; gap: 5px;
  }
  .social__rule { width: 58px; height: 1px; background: #8a8a8c; }
  .social__dot { width: 25px; height: 25px; border-radius: 50%; background: var(--paper-mark); }
</style>
</head>
<body>

<section class="card card--front">
  <div class="company-name">DULOM</div>

  <ul class="contacts">
    <li>
      <svg viewBox="0 0 24 24" aria-hidden="true"><path d="M6.6 10.8c1.4 2.8 3.8 5.1 6.6 6.6l2.2-2.2c.3-.3.7-.4 1-.2 1.1.4 2.3.6 3.6.6.6 0 1 .4 1 1V20c0 .6-.4 1-1 1C10.6 21 3 13.4 3 4c0-.6.4-1 1-1h3.5c.6 0 1 .4 1 1 0 1.3.2 2.5.6 3.6.1.3 0 .7-.2 1z"/></svg>
      1-888-DULOM-47
    </li>
    <li>
      <svg viewBox="0 0 24 24" aria-hidden="true"><path d="M7 1h10c1.1 0 2 .9 2 2v18c0 1.1-.9 2-2 2H7c-1.1 0-2-.9-2-2V3c0-1.1.9-2 2-2zm0 3v14h10V4H7zm5 15.2a1 1 0 1 0 0 2 1 1 0 0 0 0-2z"/></svg>
      317-555-0193
    </li>
    <li>
      <svg viewBox="0 0 24 24" aria-hidden="true"><path d="M2 5h20v14H2V5zm2 2v.5l8 5 8-5V7H4zm0 2.8V17h16V9.8l-8 5-8-5z"/></svg>
      info@dulomhome.com
    </li>
    <li>
      <svg viewBox="0 0 24 24" aria-hidden="true"><path d="M12 2a10 10 0 1 0 0 20 10 10 0 0 0 0-20zm-1 17.9A8 8 0 0 1 4.2 10.6L9 15.4v1c0 1.1.9 2 2 2v1.5zm6.9-2.5c-.3-.8-1-1.4-1.9-1.4h-1v-3c0-.6-.4-1-1-1H8v-2h2c.6 0 1-.4 1-1V7h2c1.1 0 2-.9 2-2v-.4a8 8 0 0 1 2.9 12.8z"/></svg>
      www.dulomhome.com
    </li>
  </ul>

  <div class="person">
    <div class="person__name">Karim Feltous</div>
    <div class="person__role">CEO / General Contractor</div>
  </div>

  <div class="edge edge--red"></div>
  <div class="edge edge--dark"></div>
</section>

<section class="card card--back">
  <div class="back-mark">
    <div class="back-mark__square"></div>
    <div class="back-mark__name">DULOM</div>
  </div>
  <p class="credentials">LICENSED | INSURED | BONDED</p>
  <div class="social">
    <span class="social__rule"></span>
    <span class="social__dot"></span>
    <span class="social__dot"></span>
    <span class="social__dot"></span>
    <span class="social__rule"></span>
  </div>
</section>

</body>
</html>
```